Sale- Bundle signs

We are looking for a design to use for Permanent SALE/Bundle deal signs. We are a natural bath products company who uses all natural ingredients to create our handmade line of natural products. We love a clean, fresh look and feel. Simple eye-catching that will be a quick glance and they will know the offer.
We would like to have something simple, eye catching that will promote sales on our different products.
Dead Sea Salt Body Scrubs
large 2 for $40
small 3 for $20
Moisturizing Wash with coconut & olive oil
2 for $20
There are several more needed but we are hoping to decide on one template before making all of the signs.
Visit our website here www.tamberlinewash.com
Target Market(s)
Our store serves 70% women and the majority of our customers are 30+ years old.
Industry/Entity Type
It Company
Other font styles liked:
- Century Gothic or similar
Look and feel
Each slider illustrates characteristics of the customer's brand and the style your logo design should communicate.

```html
<!DOCTYPE html>
<html lang="en">
<head>
<meta charset="utf-8">
<title>Tamberline – Bundle Sale Sign</title>
<link rel="stylesheet" href="https://fonts.googleapis.com/css2?family=Arimo:wght@400;700&display=swap">
<style>
  :root {
    --page-bg: #ffffff;
    --wood-dark: #3f2414;
    --wood-mid: #5a3520;
    --wood-light: #6e4328;
    --panel-center: #fffef2;
    --panel-edge: #f7ef9e;
    --ink: #141414;
    --offer-orange: #f07c1a;
    --rule: #333333;
    --footer-text: #ffffff;
  }
  * { margin: 0; padding: 0; box-sizing: border-box; }
  html, body {
    width: 1068px;
    height: 1200px;
    overflow: hidden;
    background: var(--page-bg);
  }
  .canvas {
    position: relative;
    width: 1068px;
    height: 1200px;
  }
  .sign-board {
    position: absolute;
    left: 181px;
    top: 80px;
    width: 720px;
    height: 1008px;
    background: linear-gradient(90deg, var(--wood-dark) 0%, var(--wood-mid) 35%, var(--wood-light) 55%, var(--wood-mid) 80%, var(--wood-dark) 100%);
  }
  .offer-panel {
    position: absolute;
    left: 240px;
    top: 136px;
    width: 603px;
    height: 896px;
    background: radial-gradient(ellipse at 50% 30%, var(--panel-center) 0%, #fdfbd8 45%, var(--panel-edge) 100%);
  }
  .line {
    position: absolute;
    left: 240px;
    width: 603px;
    text-align: center;
    white-space: nowrap;
    line-height: 1;
    font-family: "Arimo", Arial, sans-serif;
  }
  .brand-name {
    top: 190px;
    font-weight: 700;
    font-size: 80px;
    color: var(--ink);
  }
  .brand-tagline {
    top: 288px;
    font-weight: 400;
    font-size: 28px;
    letter-spacing: 3px;
    color: var(--ink);
  }
  .product-title {
    font-weight: 700;
    font-size: 24px;
    color: var(--ink);
  }
  .size-label {
    font-weight: 400;
    font-size: 44px;
    color: var(--ink);
  }
  .price {
    font-weight: 700;
    font-size: 72px;
    color: var(--offer-orange);
  }
  .price-large { font-size: 80px; }
  .scrub-title { top: 394px; }
  .large-label { top: 442px; }
  .large-price { top: 502px; }
  .small-label { top: 590px; }
  .small-price { top: 643px; }
  .section-rule {
    position: absolute;
    left: 288px;
    top: 733px;
    width: 474px;
    height: 2px;
    background: var(--rule);
  }
  .wash-title-1 { top: 760px; }
  .wash-title-2 { top: 793px; }
  .wash-title-3 { top: 826px; }
  .wash-price { top: 868px; }
  .website {
    top: 1048px;
    font-weight: 700;
    font-size: 22px;
    color: var(--footer-text);
  }
</style>
</head>
<body>
  <main class="canvas">
    <div class="sign-board" role="img" aria-label="Dark brown wooden plank background"></div>
    <section class="offer-panel"></section>

    <h1 class="line brand-name">Tamberline</h1>
    <p class="line brand-tagline">NATURAL BATH PRODUCTS</p>

    <h2 class="line product-title scrub-title">DEAD SEA SALT BODY SCRUBS</h2>
    <p class="line size-label large-label">Large 2</p>
    <p class="line price large-price">for $40</p>
    <p class="line size-label small-label">Small 3</p>
    <p class="line price small-price">for $20</p>

    <div class="section-rule"></div>

    <h2 class="line product-title wash-title-1">MOISTURIZING WASH</h2>
    <p class="line product-title wash-title-2">WITH</p>
    <p class="line product-title wash-title-3">COCONUT &amp; OLIVE OIL</p>
    <p class="line price price-large wash-price">2 for $20</p>

    <p class="line website">www.tamberlinewash.com</p>
  </main>
</body>
</html>
```